Lantern of Reeds: Book Cover Design + 6-Pages

**** PLEASE READ entire design brief attached!!!!!

Design Brief
A full colour digitally printed LANDSCAPE 8" (h) x 11"(w) hard cover book

1. Design front cover

PLUS

2. Design 6-pages

What is the book all about?
The Lantern of Reeds is a book for a young Goddess (aged 9 to 14 years old) approaching their first bleeding cycle. It is her time to learn about the women’s menstrual cycle and discover how it is the most earthly cycle women have and how it connects us to our intuition and to the wisdom of the moon.

Attached:
1. Complete brief
2. Front cover concept and suggested font

Target Market(s)

Target Market – women buying the Lantern of Reeds for a young girl aged 9 - 14
• Mother, mid-wife, auntie, grandmother, feminist, god mother, friend, sisters, nieces, cousins
• Yuppie hippy
• Disposable income
• Educated
• Travel overseas
• Have all new technology gadgets – brellix Cast, Zumaphone, Zumatabs, Brellix Cast etc
• New aged, spiritual
• Grass roots, shop local, home grown
• Feminist
• Educated
• Disposable income
• Yoga, Pilates, eat organically
• Value family and togetherness
• Value authentic gift giving

Industry/Entity Type

Landscape

Requirements
Nice to have
• I am looking for a wow factor (stunning, bold, striking, beautiful coffee table book) in the design because this is going to be a high quality gift.
There is a Goddess, spiritual fantasy theme.
I have supplied the front cover image that you may consider using, however I am open to your interpretation and creativity so you do not have to use this image if you do not wish.
I would like the design of this book to be universal as the story is to be translated into a number of languages.
Should not have
• Even though the book is for a 9 to 13 year girl, I am not looking for illustrations/animation

```html
<!DOCTYPE html>
<html lang="la">
<head>
<meta charset="utf-8">
<title>Lantern of Reeds — Spread</title>
<link href="https://fonts.googleapis.com/css2?family=Cabin:wght@400&family=Great+Vibes&display=swap" rel="stylesheet">
<style>
  :root {
    --backdrop: #e9e4dc;
    --sky-deep: #2f6fa8;
    --sky-light: #bfe3f2;
    --mist: #e7dbe8;
    --rose: #d9c3cf;
    --valley: #5f6b78;
    --ground: #3e4a55;
    --ink-teal: #1596b2;
    --ink-violet: #5b3c8c;
    --gutter-shade: rgba(40, 40, 60, 0.28);
  }
  html, body {
    margin: 0;
    width: 1200px;
    height: 789px;
    overflow: hidden;
    background: var(--backdrop);
  }
  .canvas {
    position: relative;
    width: 1200px;
    height: 789px;
  }
  .spread {
    position: absolute;
    left: 20px;
    top: 180px;
    width: 1160px;
    height: 430px;
    display: flex;
    box-shadow: 0 6px 18px rgba(0,0,0,0.25);
  }
  .page {
    position: relative;
    width: 580px;
    height: 430px;
    overflow: hidden;
    font-family: "Cabin", "Trebuchet MS", sans-serif;
    font-size: 13px;
  }
  .page-artwork {
    position: absolute;
    inset: 0;
  }
  .page--left .page-artwork {
    background:
      radial-gradient(ellipse 38% 45% at 14% 30%, var(--rose), transparent 70%),
      radial-gradient(ellipse 35% 30% at 60% 22%, var(--sky-light), transparent 75%),
      linear-gradient(180deg, var(--sky-deep) 0%, var(--mist) 40%, #d8cfe0 62%, var(--valley) 88%, var(--ground) 100%);
  }
  .page--right .page-artwork {
    background:
      radial-gradient(ellipse 38% 45% at 86% 30%, var(--rose), transparent 70%),
      radial-gradient(ellipse 35% 30% at 40% 22%, var(--sky-light), transparent 75%),
      linear-gradient(180deg, var(--sky-deep) 0%, var(--mist) 40%, #d8cfe0 62%, var(--valley) 88%, var(--ground) 100%);
  }
  .page--left::after,
  .page--right::after {
    content: "";
    position: absolute;
    top: 0; bottom: 0;
    width: 24px;
  }
  .page--left::after { right: 0; background: linear-gradient(90deg, transparent, var(--gutter-shade)); }
  .page--right::after { left: 0; background: linear-gradient(270deg, transparent, var(--gutter-shade)); }
  .passage {
    position: absolute;
    margin: 0;
  }
  .passage--teal { color: var(--ink-teal); }
  .passage--violet { color: var(--ink-violet); }
  .drop-cap {
    font-family: "Great Vibes", cursive;
    font-size: 30px;
    line-height: 0;
  }
  .left-opening {
    left: 170px;
    top: 56px;
    width: 300px;
    text-align: center;
    line-height: 26px;
  }
  .left-body {
    left: 80px;
    top: 208px;
    width: 400px;
    text-align: center;
    line-height: 21px;
  }
  .right-opening {
    left: 37px;
    top: 80px;
    width: 360px;
    text-align: left;
    line-height: 20.5px;
  }
  .right-body {
    right: 41px;
    top: 198px;
    width: 440px;
    text-align: right;
    line-height: 20.5px;
  }
</style>
</head>
<body>
<main class="canvas">
  <section class="spread">
    <article class="page page--left">
      <div class="page-artwork" role="img" aria-label="Dreamlike sky with a large planet and moons above misty mountains, a praying elder woman at the left edge"></div>
      <p class="passage passage--teal left-opening"><span class="drop-cap">E</span>n, quæ prodigia,<br>ex oris allata remotis! Oras<br>adveniunt pavefacta per æquora<br>nostras! Non equidem priscæ sæclum<br>rediisse videtur Pyrrhæ, cum Proteus<br>pecus altos visere montes Et sylvas, egit.</p>
      <p class="passage passage--violet left-body"><span class="drop-cap">S</span>ed tempora vix leviora Adsunt, evulsi quando radicitus alti<br>In mare descendunt montes, fluctusque pererrant. Quid vero hoc<br>monstri est magis et mirabile visu? Splendentes video, ceu pulchro<br>ex ære vel auro Conflatos, rutilisque accinctos undique gemmis,<br>Baccâ cærulea, et flammas imitante pyropo. Ex oriente adsunt, ubi<br>gazas optima tellus Parturit omnigenas, quibus æva per omnia<br>sumptu Ingenti finxere sibi diademata reges?<br>Vix hoc crediderim. Non fallunt talia acutos</p>
    </article>
    <article class="page page--right">
      <div class="page-artwork" role="img" aria-label="Dreamlike sky with a planet and moons over a mountain valley, a praying elder woman at the right edge"></div>
      <p class="passage passage--teal right-opening"><span class="drop-cap">M</span>ercatorum oculos:&nbsp; prius et quam littora<br>Gangis Liquissent, avidis gratissima præda fuissent.<br>Ortos unde putemus?&nbsp; An illos Ves’vius atrox Protulit,<br>ignivomisve ejecit faucibus Ætna? Luce micant propria,<br>Phœbive, per aëra purum</p>
      <p class="passage passage--violet right-body"><span class="drop-cap">N</span>unc stimulantis equos, argentea tela retorquent?<br>Phœbi luce micant.&nbsp; Ventis et fluctibus altis Appulsi, et rapidis subter<br>currentibus undis, Tandem non fallunt oculos.&nbsp; Capita alta videre est<br>Multa onerata nive et canis conspersa pruinis.<br>Cætera sunt glacies.&nbsp; Procul hinc, ubi Bruma</p>
    </article>
  </section>
</main>
</body>
</html>
```